Verdora Cookbook Cover

I need a design (front and back) for a cookbook cover. Our partners are looking for a few ideas to pick from.
You can see the style for one of the cookbooks we currently carry - uploaded with this brief.
This cookbook is a little different than most cookbooks out there. It is a cancer-fighting cookbook but we don't want it to be so cancer focused that people who don't have cancer will not buy. The book starts out with a section for Foods that Help, then goes to another section called Foods that Hurt. Then, we provide a Recipes section from the ingredients found in Foods that Help. Finally, the last section is called Beyond the Plate and deals with healthy lifestyle habits. You can see a rough draft of the content of the book at the link below. Please keep in mind that the current covers you see are not at all what we want. These were just put there to fill in the space.
Link for cookbook content: https://www.filecrate-share.com/s/4kq92xpwt7bnrvd/The%20Sunlit%20Table%20-%20EDITED.pdf?dl=0
The title: The Sunlit Table
Subtitle: Fighting Cancer One Meal at a Time
Author: Mirela Tosk
The company that puts the book out is Verdora. It would be nice to have the logo somewhere small. Logo can be found here: https://www.filecrate-share.com/s/mz83ntbq2vhxe5a/Verdora%20Logo%20%26%20Guidelines.zip?dl=0
Like "Bring Home a Brighter Bowl" attached to this brief, we do NOT want something somber but more on the bright side. Just make it look nice and fresh. It would also be nice to somehow incorporate the concept of the cancer ribbon or a silhouette of it in a way that is not upfront but can still be acknowledge. No need for it to be pink and if that does not work, than it's better just to leave it out.
For the back cover, you can design it but simply leave room for us to fill in some text. No need for a spine design as it will be spiral bound.
The file must be designed and saved in PHOTOSHOP format.
According to the designer, the dimensions are:
207mm x 270mm + 5mm bleed
If you want to use the recipe pictures somehow in the cover, just snatch a picture from the content PDF and we can always replace it with the original larger file at a later time. Unfortunately, I don't have the pictures uploaded in filecrate.

```html
<!DOCTYPE html>
<html lang="en">
<head>
<meta charset="utf-8">
<title>The Sunlit Table — Cookbook Cover Spread</title>
<link rel="stylesheet" href="https://fonts.googleapis.com/css2?family=Anton&family=Questrial&display=swap">
<style>
  :root {
    --berry-blue: #6570c8;
    --berry-blue-light: #8d96e0;
    --berry-red: #ec3358;
    --berry-pink: #ff5a78;
    --berry-black: #2b2236;
    --wood-dark: #6b4f3d;
    --wood-mid: #8d6d56;
    --linen: #f6f3ee;
    --plate: #f7f5f0;
    --ribbon-pink: #f05bb8;
    --title-red: #d0203f;
    --title-purple: #5b3a8e;
    --title-green: #4aa22f;
    --white: #ffffff;
  }
  * { box-sizing: border-box; margin: 0; padding: 0; }
  html, body { width: 1200px; height: 802px; overflow: hidden; background: #ffffff; }
  .spread { position: relative; width: 1200px; height: 802px; overflow: hidden; font-family: "Questrial", sans-serif; }

  /* Back cover */
  .back-cover { position: absolute; left: 0; top: 0; width: 586px; height: 802px; overflow: hidden; }
  .back-cover__photo {
    position: absolute; inset: 0;
    background:
      radial-gradient(circle at 10% 14%, var(--berry-red) 0 80px, transparent 120px),
      radial-gradient(circle at 50% 8%, var(--berry-pink) 0 60px, transparent 100px),
      radial-gradient(circle at 52% 22%, var(--berry-black) 0 70px, transparent 115px),
      radial-gradient(circle at 85% 12%, var(--berry-red) 0 60px, transparent 100px),
      radial-gradient(circle at 60% 58%, var(--berry-blue-light) 0 80px, transparent 125px),
      radial-gradient(circle at 88% 50%, var(--berry-red) 0 50px, transparent 95px),
      radial-gradient(circle at 12% 52%, var(--berry-black) 0 70px, transparent 120px),
      radial-gradient(circle at 80% 72%, var(--berry-pink) 0 70px, transparent 115px),
      radial-gradient(circle at 40% 92%, var(--berry-red) 0 95px, transparent 140px),
      radial-gradient(circle at 88% 92%, var(--berry-black) 0 60px, transparent 105px),
      radial-gradient(circle at 10% 86%, var(--berry-blue-light) 0 60px, transparent 105px),
      linear-gradient(160deg, var(--berry-blue-light), var(--berry-blue));
  }
  .back-cover__panel {
    position: absolute; left: 104px; top: 176px; width: 348px; height: 424px;
    border: 1px solid rgba(255,255,255,0.45); border-radius: 14px;
    background: rgba(90,100,180,0.22);
  }
  .back-cover__heading {
    position: absolute; left: 104px; top: 206px; width: 348px;
    text-align: center; color: var(--white); font-size: 15px; line-height: 1.15;
  }

  /* Partner mark */
  .partner-mark { position: absolute; display: flex; flex-direction: column; align-items: center; gap: 14px; color: var(--white); font-size: 10.5px; white-space: nowrap; }
  .partner-mark__dot { width: 24px; height: 24px; border-radius: 50%; background: var(--ribbon-pink); }
  .partner-mark--back { left: 178px; top: 510px; width: 200px; }
  .partner-mark--front { left: 4px; top: 732px; width: 136px; }

  /* Front cover */
  .front-cover { position: absolute; left: 586px; top: 0; width: 614px; height: 802px; overflow: hidden; }
  .front-cover__photo {
    position: absolute; inset: 0;
    background:
      radial-gradient(ellipse at 25% 4%, #e6c995 0 80px, transparent 120px),
      radial-gradient(ellipse at 55% 12%, var(--linen) 0 170px, transparent 240px),
      radial-gradient(circle at 94% 14%, #ffffff 0 60px, transparent 110px),
      radial-gradient(circle at 6% 32%, #ffffff 0 22px, transparent 40px),
      radial-gradient(circle at 94% 84%, #ffffff 0 50px, transparent 90px),
      radial-gradient(circle at 80% 80%, #e8414a 0 38px, transparent 62px),
      repeating-linear-gradient(90deg, rgba(255,255,255,0.06) 0 2px, transparent 2px 44px),
      linear-gradient(180deg, var(--wood-mid), var(--wood-dark));
  }
  .front-cover__plate {
    position: absolute; left: 142px; top: 200px; width: 384px; height: 384px;
    border-radius: 50%; background: var(--plate); opacity: 0.95;
  }
  .book-title { position: absolute; left: 0; top: 0; width: 614px; height: 560px; font-family: "Anton", sans-serif; text-transform: uppercase; font-weight: 400; }
  .book-title__line { position: absolute; line-height: 1; white-space: nowrap; text-shadow: 0 0 6px rgba(255,255,255,0.9); }
  .book-title__the { left: 230px; top: 212px; font-size: 98px; color: var(--title-red); letter-spacing: 4px; }
  .book-title__sunlit { left: 0; top: 316px; width: 614px; text-align: center; font-size: 116px; color: var(--title-purple); letter-spacing: 30px; padding-left: 30px; }
  .book-title__table { left: 146px; top: 432px; font-size: 110px; color: var(--title-green); letter-spacing: 6px; }

  .book-subtitle { position: absolute; left: 120px; top: 614px; width: 370px; text-align: center; color: var(--white); font-size: 21px; text-shadow: 0 1px 3px rgba(0,0,0,0.45); }

  .publisher-mark {
    position: absolute; left: 136px; top: 746px; height: 30px; padding: 0 12px;
    display: flex; align-items: center; border-radius: 15px; background: var(--white);
    color: var(--title-purple); font-size: 14px;
  }

  .author { position: absolute; left: 500px; top: 698px; width: 100px; display: flex; flex-direction: column; align-items: center; color: var(--white); font-size: 10.5px; line-height: 1.15; text-align: center; }
  .author__portrait { width: 68px; height: 68px; border-radius: 50%; border: 2px solid var(--white); background: radial-gradient(circle at 50% 40%, #b08a6c, #6a4a38); margin-bottom: 4px; }
</style>
</head>
<body>
<main class="spread">
  <section class="back-cover">
    <div class="back-cover__photo" role="img" aria-label="Close-up photo of raspberries, blueberries and blackberries"></div>
    <div class="back-cover__panel"></div>
    <p class="back-cover__heading">Acknowledgements<br>&amp; Back Cover Information</p>
    <div class="partner-mark partner-mark--back">
      <span class="partner-mark__dot"></span>
      <span class="partner-mark__name">Northfield Cancer Alliance</span>
    </div>
  </section>

  <section class="front-cover">
    <div class="front-cover__photo" role="img" aria-label="Overhead photo of a wooden table with oat cookies, embroidered linen, daisies, an apple and a spoon of raspberries"></div>
    <div class="front-cover__plate"></div>
    <h1 class="book-title">
      <span class="book-title__line book-title__the">The</span>
      <span class="book-title__line book-title__sunlit">Sunlit</span>
      <span class="book-title__line book-title__table">Table</span>
    </h1>
    <p class="book-subtitle">Fighting Cancer One Meal at a Time</p>
    <div class="partner-mark partner-mark--front">
      <span class="partner-mark__dot"></span>
      <span class="partner-mark__name">Northfield Cancer Alliance</span>
    </div>
    <div class="publisher-mark">Verdora</div>
    <div class="author">
      <div class="author__portrait" role="img" aria-label="Author portrait"></div>
      <span>Author:</span>
      <span>Mirela Tosk</span>
    </div>
  </section>
</main>
</body>
</html>
```